Velmora Systems Website

Website design for our company: Velmora Systems.
The website should look fresh and IT focused. Please have a look at http://www.velmorasystems.example.au/ for our current design. We want something fresh and new, professional looking, in WordPress so we can easily make changes.

It Company

```html
<!DOCTYPE html>
<html lang="en">
<head>
<meta charset="utf-8">
<title>Velmora Systems</title>
<link href="https://fonts.googleapis.com/css2?family=Ubuntu:wght@400;500&family=Arimo:wght@400;700&display=swap" rel="stylesheet">
<style>
:root{
  --blue:#0d6ec3;
  --blue-dark:#0a5aa3;
  --green:#13a84a;
  --grey-band:#cacaca;
  --light-band:#f1f1f1;
  --text:#3a3a3a;
  --rule:#bdbdbd;
  --footer:#1c1c1c;
  --footer-text:#c9c9c9;
}
*{box-sizing:border-box;margin:0;padding:0}
html,body{width:1148px;height:1200px;overflow:hidden;background:#fff}
body{position:relative;font-family:"Arimo",Arial,sans-serif;color:var(--text)}
.abs{position:absolute}
h2.section-title{position:absolute;font-family:"Ubuntu",sans-serif;font-weight:500;font-size:22px;color:var(--blue)}
h2.section-title span{color:var(--green)}
.rule{position:absolute;height:1px;background:var(--rule)}

/* header */
.logo{left:170px;top:22px;display:flex;align-items:center;gap:8px}
.logo-square{width:30px;height:30px;background:var(--green);border-radius:3px}
.logo-name{font-family:"Ubuntu",sans-serif;font-weight:500;font-size:22px;color:var(--green)}
.phone{right:163px;top:26px;display:flex;align-items:center;gap:6px;font-family:"Ubuntu",sans-serif;font-weight:500;font-size:19px;color:#111}
.search{left:809px;top:68px;width:178px;height:26px;border:1px solid #cfcfcf;font-size:11px;font-style:italic;color:#555;padding:6px 8px}
.search svg{position:absolute;right:6px;top:5px}

/* nav + hero */
.grey-band{left:0;top:112px;width:1148px;height:358px;background:var(--grey-band)}
.nav{left:160px;top:112px;width:828px;height:38px;background:var(--blue);display:flex}
.nav a{font-family:"Ubuntu",sans-serif;font-size:14px;color:#fff;text-decoration:none;display:flex;align-items:center;justify-content:center;border-right:1px solid #2b82cf}
.nav a.active{background:var(--green)}
.hero{left:160px;top:150px;width:828px;height:364px;background:linear-gradient(90deg,#1b63b8 0%,#4a95dc 40%,#8aa0b8 70%,#6c7480 100%)}
.hero-arrow{top:283px;width:32px;height:32px;border-radius:50%;background:#1a1a1a}
.hero-arrow svg{position:absolute;left:10px;top:9px}
.hero-caption{left:160px;top:470px;width:828px;height:44px;background:rgba(13,82,160,.9);color:#fff;font-family:"Ubuntu",sans-serif;font-size:22px;text-align:center;line-height:44px}

/* about */
.about-photo{left:170px;top:581px;width:243px;height:112px;background:linear-gradient(135deg,#c8ccd2,#7d8794 55%,#2d333c)}
.about-text{left:170px;top:585px;width:519px;font-size:10.2px;line-height:16px;text-align:justify}
.about-text .float{float:left;width:258px;height:112px}
.more{font-size:10.5px;color:var(--green)}

/* services */
.services{left:730px;top:585px;width:250px;list-style:none}
.services li{display:flex;align-items:center;height:41px;font-family:"Ubuntu",sans-serif;font-size:16px;color:#222}
.services svg{width:30px;margin-right:16px}

/* clients band */
.light-band{left:0;top:808px;width:1148px;height:160px;background:var(--light-band)}
.client{top:892px;font-family:"Ubuntu",sans-serif;font-weight:500;font-size:19px;color:#555;display:flex;align-items:center;gap:6px}
.client i{display:block;width:14px;height:14px;background:#888}
.code-input{left:729px;top:875px;width:244px;height:25px;background:#fff;border:1px solid #ccc;font-size:10px;font-style:italic;color:#777;padding:6px 10px}
.connect{left:729px;top:909px;width:88px;height:21px;background:var(--green);color:#fff;font-family:"Ubuntu",sans-serif;font-size:12.5px;text-align:center;line-height:21px}

/* footer */
.footer{left:0;top:968px;width:1148px;height:198px;background:var(--footer)}
.footer h3{position:absolute;font-family:"Ubuntu",sans-serif;font-weight:400;font-size:13px;color:#eee;top:17px}
.vline{position:absolute;top:28px;width:1px;height:145px;background:#444}
.links{position:absolute;left:169px;top:43px;width:115px;list-style:none}
.links li{height:20.3px;border-bottom:1px solid #444;font-size:10px;color:var(--footer-text);padding:4px 0 0 13px;position:relative}
.links li:last-child{border:none}
.links li:before{content:"";position:absolute;left:1px;top:8px;border-left:4px solid #999;border-top:3px solid transparent;border-bottom:3px solid transparent}
.quote{position:absolute;left:324px;top:45px;width:272px;font-size:10.5px;line-height:15.3px;color:#b9b9b9}
.author{position:absolute;left:324px;top:132px;width:272px;text-align:right;font-size:10.5px;line-height:13.5px;font-weight:700;color:#9c9c9c}
.contact-row{position:absolute;left:651px;display:flex;gap:9px;font-size:10px;line-height:14px;color:#e2e2e2}
.contact-row i{display:block;width:19px;height:19px;border-radius:50%;background:var(--blue);position:relative;flex:none}
.social{position:absolute;top:42px;width:25px;height:25px;border-radius:50%;background:#3a3a3a}
.social.on{background:var(--green)}
.f-logo{position:absolute;left:850px;top:94px;width:128px;height:63px;background:#fff;border-radius:4px;display:flex;align-items:center;justify-content:center;gap:6px;font-family:"Ubuntu",sans-serif;font-weight:500;font-size:14px;color:var(--green)}
.f-logo b{display:block;width:18px;height:18px;background:var(--green);border-radius:2px}
.copyright{left:0;top:1166px;width:1148px;height:34px;background:var(--blue);color:#fff;font-size:10.3px;text-align:center;line-height:34px}
</style>
</head>
<body>

<header>
  <div class="abs logo"><span class="logo-square"></span><span class="logo-name">Velmora Systems</span></div>
  <div class="abs phone">
    <svg width="20" height="20" viewBox="0 0 20 20"><circle cx="10" cy="10" r="8.5" fill="none" stroke="#1660b8" stroke-width="1.6"/><path d="M7 5.5c-1 1-1 3 1 6s4 4 5.5 3l.8-1-2-1.6-1 .7c-1-.5-2.3-2-2.7-3l.8-.8L8.3 5z" fill="#1660b8"/></svg>
    014-555-0172
  </div>
  <div class="abs search">search
    <svg width="14" height="14" viewBox="0 0 14 14"><circle cx="6" cy="6" r="4.3" fill="none" stroke="#999" stroke-width="1.6"/><path d="M9 9l4 4" stroke="#999" stroke-width="2"/></svg>
  </div>
</header>

<div class="abs grey-band"></div>
<nav class="abs nav">
  <a class="active" style="width:94px">HOME</a>
  <a style="width:120px">ABOUT US</a>
  <a style="width:113px">SERVICES</a>
  <a style="width:116px">SUPPORT</a>
  <a style="width:146px">TESTIMONIALS</a>
  <a style="width:107px">CLIENTS</a>
  <a style="width:132px;border:none">CONTACT US</a>
</nav>
<div class="abs hero" role="img" aria-label="Business consultant touching a digital interface over a world map"></div>
<div class="abs hero-arrow" style="left:174px"><svg width="10" height="14"><path d="M8 1L2 7l6 6" fill="none" stroke="#fff" stroke-width="1.5"/></svg></div>
<div class="abs hero-arrow" style="left:942px"><svg width="10" height="14"><path d="M2 1l6 6-6 6" fill="none" stroke="#fff" stroke-width="1.5"/></svg></div>
<div class="abs hero-caption">WE HAVE SPECIALISED ENGINEERS, TRAINED TO DO SPECIALISED WORK</div>

<section>
  <h2 class="section-title" style="left:170px;top:540px">About <span>Velmora Systems</span></h2>
  <div class="rule" style="left:170px;top:570px;width:524px"></div>
  <div class="abs about-photo" role="img" aria-label="Team of colleagues in a business meeting"></div>
  <p class="abs about-text"><span class="float"></span>Velmora Systems is an Adelaide based company with a single objective - to excel in the support and service of all computer and IT needs. Our core business includes information technology consultation, equipment and software optimisation, network system and application software system construction, overall system network routine maintenance and management. We are currently supporting over 200 businesses through a variety of service level agreements and support plans. We provide a high level consulting service using the most experienced engineers at a reasonable and fair price. We believe in using a Business Value approach to every aspect of computer consulting to provide our clients with the most cost-effective solutions. We understand that no one business is the same and our IT service can be tailored to fit individual requirements.</p>
  <div class="abs more" style="left:636px;top:775px">Read More...</div>

  <h2 class="section-title" style="left:730px;top:541px">Our <span>Services</span></h2>
  <div class="rule" style="left:730px;top:570px;width:250px"></div>
  <ul class="abs services">
    <li><svg viewBox="0 0 30 26" height="26"><path d="M4 22L18 8M8 4l6 6M20 4l4 4-12 12-4-4z" fill="none" stroke="#333" stroke-width="3"/></svg>ON-SITE SERVICE</li>
    <li><svg viewBox="0 0 30 26" height="26"><rect x="2" y="3" width="20" height="14" fill="none" stroke="#333" stroke-width="2"/><path d="M8 22h10" stroke="#333" stroke-width="2"/><circle cx="23" cy="18" r="6" fill="#fff" stroke="#333" stroke-width="2"/></svg>REMOTE DESKTOP</li>
    <li><svg viewBox="0 0 30 26" height="26"><path d="M3 3v8a6 6 0 0012 0V3M9 17v3a5 5 0 0010 0v-6" fill="none" stroke="#333" stroke-width="2"/><circle cx="22" cy="8" r="4" fill="none" stroke="#333" stroke-width="2"/></svg>MEDICAL IT SERVICE</li>
    <li><svg viewBox="0 0 30 26" height="26"><rect x="2" y="3" width="20" height="14" fill="none" stroke="#333" stroke-width="2"/><circle cx="21" cy="17" r="4" fill="#fff" stroke="#333" stroke-width="2"/><path d="M24 20l4 4" stroke="#333" stroke-width="2.5"/></svg>PHARMACY IT SERVICE</li>
    <li><svg viewBox="0 0 30 26" height="26"><rect x="2" y="5" width="22" height="14" fill="none" stroke="#333" stroke-width="2"/><path d="M10 24h8M10 15l14-13" stroke="#333" stroke-width="2"/></svg>WEBSITE DESIGN</li>
  </ul>
  <div class="abs more" style="left:927px;top:775px">View All...</div>
</section>

<section>
  <div class="abs light-band"></div>
  <h2 class="section-title" style="left:169px;top:835px">Our <span>Clients</span></h2>
  <svg class="abs" style="left:673px;top:844px" width="32" height="14"><path d="M6 1L1 7l5 6M26 1l5 6-5 6" fill="none" stroke="#555" stroke-width="1.4" transform="translate(0,0)"/><path d="M26 1l5 6-5 6" fill="none" stroke="var(--green)" stroke-width="1.4"/></svg>
  <div class="rule" style="left:169px;top:864px;width:540px"></div>
  <div class="abs client" style="left:171px"><i></i>Northwind</div>
  <div class="abs client" style="left:337px"><i></i>cloudvale</div>
  <div class="abs client" style="left:510px">QXR</div>
  <div class="abs client" style="left:622px">BRANTO</div>

  <h2 class="section-title" style="left:729px;top:837px">Remote <span>Support</span></h2>
  <div class="rule" style="left:729px;top:864px;width:250px"></div>
  <div class="abs code-input">Enter your 6 digit code</div>
  <div class="abs connect">Connect Now</div>
</section>

<footer class="abs footer">
  <h3 style="left:169px">Main Links</h3>
  <ul class="links">
    <li>Home</li><li>About Us</li><li>Services</li><li>Support</li><li>Testimonials</li><li>Clients</li><li>Contact</li>
  </ul>
  <div class="vline" style="left:295px"></div>

  <h3 style="left:324px">Testimonials</h3>
  <svg style="position:absolute;left:575px;top:20px" width="24" height="12"><path d="M5 1L1 6l4 5M19 1l4 5-4 5" fill="none" stroke="#ccc" stroke-width="1.3"/></svg>
  <p class="quote">&ldquo; I have always found the team extremely helpful with their advice over the phone. They also have the ability to access our computers remotely, and can rectify most problems quite swiftly. I have no hesitation in recommending Velmora Systems for all of your IT needs. &rdquo;</p>
  <p class="author">Daniel Ortway B.Pharm<br>Greenfield Community Pharmacy, Kestrel Park</p>
  <div class="vline" style="left:625px"></div>

  <h3 style="left:651px">Contact Info</h3>
  <div class="contact-row" style="top:44px"><i></i><span>27 Harbour Lane<br>Kestrel Park<br>5090 Australia</span></div>
  <div class="contact-row" style="top:97px;align-items:center"><i></i><span>088-555-0194</span></div>
  <div class="contact-row" style="top:131px;align-items:center"><i></i><span>support@velmorasystems.example</span></div>
  <div class="vline" style="left:821px"></div>

  <h3 style="left:851px">Follow Us On</h3>
  <div class="social on" style="left:851px" aria-label="Social profile"></div>
  <div class="social" style="left:883px" aria-label="Social profile"></div>
  <div class="social" style="left:914px" aria-label="Social profile"></div>
  <div class="social" style="left:945px" aria-label="Social profile"></div>
  <div class="f-logo"><b></b>Velmora Systems</div>
</footer>

<div class="abs copyright">Copyright 2014 Velmora Systems &nbsp;|&nbsp; Terms of Use &nbsp;|&nbsp; Privacy Statement &nbsp;|&nbsp; Feedback &nbsp;|&nbsp; Legal</div>

</body>
</html>
```